Velk Partners Building Business Cards

We need a business card that reflects our business as "Solar Experts" in San Diego. Browse our website www.velkpartners.example our License needs to be displayed as "CSLB# 3867140" our phone number is (619) 555-0187

Save thousands on your electric bills and increase the value of your home while helping to protect the environment. Our solar installation experts will help you design the system that's right for you, using only the highest quality equipment that will look great and give you ideal performance. Our goal is to make you energy independent, and get your electric bill to 0.

Paul Osterby
(619) 555-0187
paul@velkpartners.example

Target Market(s)

Home owners in san diego looking for solar

Industry/Entity Type

Solar Energy

Contact Information for Business Card

Paul Osterby
(619) 555-0187
paul@velkpartners.example

Font styles to use
Other font styles liked:
• Use our logo font

Requirements
Must have
• License needs to be displayed as "CSLB# 3867140" our phone number is (619) 555-0187
Nice to have
• Real images of rooftop home solar in san diego
Should not have
• our business address

```html
<!DOCTYPE html>
<html lang="en">
<head>
<meta charset="utf-8">
<title>Velk Partners Building – Business Card</title>
<link rel="stylesheet" href="https://fonts.googleapis.com/css2?family=Libre+Franklin:wght@400;500;700;800&display=swap">
<style>
  :root {
    --page: #d9d6d2;
    --card-light: #eef0f1;
    --card-light-edge: #dfe3e6;
    --navy-top: #2b4b88;
    --navy-bottom: #13234a;
    --orange: #e58a1f;
    --logo-navy: #1b2f5c;
    --text-light: #e4e8f0;
  }
  html, body {
    margin: 0;
    width: 1200px;
    height: 969px;
    overflow: hidden;
    background: var(--page);
    font-family: "Libre Franklin", Arial, sans-serif;
  }
  .business-card {
    position: absolute;
    left: 100px;
    top: 199px;
    width: 1000px;
    height: 571px;
    background: linear-gradient(135deg, var(--card-light), var(--card-light-edge));
    box-shadow: 0 10px 30px rgba(0,0,0,0.18);
    overflow: hidden;
  }
  .card-art {
    position: absolute;
    inset: 0;
  }
  .brand-name {
    position: absolute;
    left: 520px;
    top: 92px;
    width: 400px;
    text-align: center;
    color: var(--logo-navy);
    font-weight: 800;
    font-size: 50px;
    line-height: 1.05;
    letter-spacing: -0.5px;
    margin: 0;
  }
  .contact {
    position: absolute;
    left: 60px;
    top: 222px;
    color: var(--text-light);
  }
  .contact-name {
    margin: 0;
    color: var(--orange);
    font-weight: 500;
    font-size: 31px;
  }
  .contact-role {
    margin: 6px 0 0;
    font-size: 25px;
  }
  .contact-license {
    margin: 44px 0 0;
    font-size: 24px;
    letter-spacing: 0.5px;
  }
  .contact-lines {
    list-style: none;
    margin: 30px 0 0;
    padding: 0;
  }
  .contact-lines li {
    display: flex;
    align-items: center;
    gap: 14px;
    font-size: 24px;
    height: 38px;
  }
  .contact-lines svg {
    width: 24px;
    height: 24px;
    flex: none;
  }
</style>
</head>
<body>
  <section class="business-card">
    <svg class="card-art" viewBox="0 0 1000 571" aria-hidden="true">
      <defs>
        <linearGradient id="navy-panel" x1="0" y1="0" x2="0.4" y2="1">
          <stop offset="0" stop-color="var(--navy-top)"/>
          <stop offset="1" stop-color="var(--navy-bottom)"/>
        </linearGradient>
      </defs>
      <path d="M0,0 L448,0 C371,69 345,224 431,328 C500,414 517,483 465,571 L0,571 Z" fill="url(#navy-panel)"/>
      <path d="M448,0 C371,69 345,224 431,328 C500,414 517,483 465,571 L480,571 C535,483 515,410 446,324 C368,224 395,80 458,0 Z" fill="var(--orange)"/>
    </svg>

    <h1 class="brand-name">Velk Partners<br>Building</h1>

    <div class="contact">
      <p class="contact-name">Paul Osterby</p>
      <p class="contact-role">CEO/Founder</p>
      <p class="contact-license">CSLB# 3867140</p>
      <ul class="contact-lines">
        <li>
          <svg viewBox="0 0 24 24" aria-hidden="true"><path fill="var(--orange)" d="M6.6 10.8a15 15 0 0 0 6.6 6.6l2.2-2.2c.3-.3.7-.4 1-.2 1.1.4 2.3.6 3.6.6.6 0 1 .4 1 1V20c0 .6-.4 1-1 1A17 17 0 0 1 3 4c0-.6.4-1 1-1h3.5c.6 0 1 .4 1 1 0 1.3.2 2.5.6 3.6.1.3 0 .7-.2 1z"/></svg>
          <span>(619) 555-0187</span>
        </li>
        <li>
          <svg viewBox="0 0 24 24" aria-hidden="true"><path fill="var(--orange)" d="M2 5h20v14H2z"/><path fill="none" stroke="var(--navy-bottom)" stroke-width="1.6" d="M2 5l10 8 10-8"/></svg>
          <span>paul@velkpartners.example</span>
        </li>
        <li>
          <svg viewBox="0 0 24 24" aria-hidden="true"><circle cx="12" cy="12" r="10" fill="var(--orange)"/><path fill="none" stroke="var(--navy-bottom)" stroke-width="1.4" d="M2 12h20M12 2c3 3 3 17 0 20M12 2c-3 3-3 17 0 20"/></svg>
          <span>www.velkpartners.example</span>
        </li>
      </ul>
    </div>
  </section>
</body>
</html>
```